indépendant en tant que Massothérapeute et Préparateur Mental, j'ai besoin de ...

Massothérapeute et préparateur mental indépendant, je recherche une carte de visite sobre et dynamique, sans images liées au massage ou à la préparation mentale mais intégrant mon logo. Les couleurs que j'aime bien sont : Blanc, gris, anthracite, noir et jaune

Contact Information for Business Card

carte de préférence Horizontale
neutre qui puisse toucher le deux domaines Massothérapie et préparation mentale

Requirements
Must have
• mon projet doit intégrer au recto:
LOGO
Loïc Bardèze
078 513 26 48
info@loicbardeze.ch
et éventuellement www.loicbardeze.ch

et au verso les deux adresses:

Chemin des Ormilles 7B
1400 Yverdon-les-Bains

Route de la Gravière 9
1700 Fribourg

Should not have
• mon projet ne doit pas contenir d'image en liens avec le massage ni la préparation mentale.

```html
<!DOCTYPE html>
<html lang="fr">
<head>
<meta charset="utf-8">
<title>Carte de visite – Loïc Bardèze</title>
<link rel="stylesheet" href="https://fonts.googleapis.com/css2?family=Roboto:wght@300;400;500;700&display=swap">
<style>
  :root {
    --backdrop: #3b332e;
    --card: #262628;
    --card-edge: #1c1c1e;
    --faint: #2e2e31;
    --white: #f4f4f4;
    --grey: #c9c9cc;
    --yellow: #f2c417;
  }
  * { margin: 0; padding: 0; box-sizing: border-box; }
  html, body { width: 1200px; height: 795px; overflow: hidden; }
  body {
    background: var(--backdrop);
    font-family: "Roboto", Arial, sans-serif;
    color: var(--white);
    position: relative;
  }
  .card {
    position: absolute;
    width: 520px;
    height: 336px;
    background: var(--card);
    border: 1px solid var(--card-edge);
    border-radius: 4px;
    overflow: hidden;
    box-shadow: 0 10px 30px rgba(0,0,0,.35);
  }
  .card--back { left: 50px; top: 120px; }
  .card--front { left: 630px; top: 340px; }

  /* back */
  .back-deco {
    position: absolute;
    left: 40px; top: 60px;
    font-weight: 700;
    font-size: 92px;
    line-height: 1.05;
    color: var(--faint);
    white-space: nowrap;
  }
  .addresses {
    position: absolute;
    left: 96px; top: 128px;
    list-style: none;
    font-size: 15px;
    line-height: 1.6;
  }
  .addresses li { display: flex; align-items: center; gap: 8px; }
  .addresses li:nth-child(2) { padding-left: 22px; }

  /* front */
  .brand {
    position: absolute;
    left: 40px; top: 38px;
    display: flex; align-items: center; gap: 12px;
  }
  .brand-dot { width: 22px; height: 22px; border-radius: 50%; background: var(--white); }
  .brand-name { font-weight: 700; font-size: 30px; letter-spacing: .5px; }
  .brand-tagline {
    position: absolute;
    left: 74px; top: 80px;
    font-size: 10px; letter-spacing: 1.2px;
    text-transform: uppercase; color: var(--grey);
  }
  .identity { position: absolute; left: 40px; top: 124px; }
  .identity-name { font-weight: 500; font-size: 20px; text-transform: uppercase; letter-spacing: .3px; }
  .identity-role { font-weight: 300; font-size: 16px; margin-top: 2px; }
  .contacts {
    position: absolute; left: 40px; top: 196px;
    list-style: none; font-size: 16px; line-height: 1.5;
  }
  .contacts li { display: flex; align-items: center; gap: 8px; }
  .icon { width: 12px; height: 12px; flex: none; fill: var(--yellow); }
  .front-deco {
    position: absolute;
    right: 22px; bottom: 28px;
    font-weight: 700; font-size: 40px;
    color: #202022;
    text-shadow: 0 1px 0 #353538;
  }
</style>
</head>
<body>
  <section class="card card--back" aria-label="Verso">
    <div class="back-deco" aria-hidden="true">Loïc<br>Bardèze</div>
    <ul class="addresses">
      <li>
        <svg class="icon" viewBox="0 0 12 12"><path d="M6 0a4 4 0 0 0-4 4c0 3 4 8 4 8s4-5 4-8a4 4 0 0 0-4-4zm0 5.5A1.5 1.5 0 1 1 6 2.5a1.5 1.5 0 0 1 0 3z"/></svg>
        Chemin des Ormilles 7B, 1400 Yverdon-les-Bains
      </li>
      <li>
        <svg class="icon" viewBox="0 0 12 12"><path d="M6 0a4 4 0 0 0-4 4c0 3 4 8 4 8s4-5 4-8a4 4 0 0 0-4-4zm0 5.5A1.5 1.5 0 1 1 6 2.5a1.5 1.5 0 0 1 0 3z"/></svg>
        Route de la Gravière 9, 1700 Freiburg
      </li>
    </ul>
  </section>

  <section class="card card--front" aria-label="Recto">
    <div class="brand">
      <span class="brand-dot" aria-hidden="true"></span>
      <span class="brand-name">Loïc Bardèze</span>
    </div>
    <div class="brand-tagline">Massothérapeute / Préparateur Mental</div>

    <div class="identity">
      <div class="identity-name">Loïc Bardèze</div>
      <div class="identity-role">Founder &amp; CEO</div>
    </div>

    <ul class="contacts">
      <li>
        <svg class="icon" viewBox="0 0 12 12"><path d="M2.5 0.5l2 2.5-1.2 1.3a7 7 0 0 0 4.4 4.4L9 7.5l2.5 2-1.3 2C5 11.5 0.5 7 0.5 1.8z"/></svg>
        078 513 26 48
      </li>
      <li>
        <svg class="icon" viewBox="0 0 12 12"><path d="M0 2h12v1L6 7 0 3zM0 4.3l6 4 6-4V10H0z"/></svg>
        info@loicbardeze.ch
      </li>
      <li>
        <svg class="icon" viewBox="0 0 12 12"><circle cx="6" cy="6" r="6"/><path d="M1 6h10M6 0v12" stroke="#262628" stroke-width="1"/></svg>
        www.loicbardeze.ch
      </li>
    </ul>

    <div class="front-deco" aria-hidden="true">Loïc Bardèze</div>
  </section>
</body>
</html>
```